Sales presentation introduction for Finance and Tech firms

Our business is two fold - 1) recruitment 2) consultancy. We would like a one or two page template that we can use to send to potential clients. The template will ideally be the same for the recruitment and consultancy side. We need to be able to edit the template to enter text.

I have attached our logo so you can see what we currently use on Corvella.

Sector is financial services and technology. We do not intent to have lots of text but the layout/images/designs to be used should cover some of page in a way that it takes up some space to avoid having to write lot of text.

Open to colour suggestions.

Please look at the attached word doc to see the text I would like for the two presentations.

Happy to answer questions.

Target Market(s)

Directors

Industry/Entity Type

Finance and tech companies

Colors
0094D4
00A9DD
6FCCEA
C7EBF8
E9F6FB

Requirements
Must have
• Editable text

```html
<!DOCTYPE html>
<html lang="en">
<head>
<meta charset="utf-8">
<title>Meridian Apex – Two-Page Introduction</title>
<link href="https://fonts.googleapis.com/css2?family=Open+Sans:wght@400;600;700;800&display=swap" rel="stylesheet">
<style>
:root{
  --navy:#0b4f9c;
  --blue:#0094d4;
  --blue-mid:#1a7cc8;
  --sky:#6fccea;
  --pale:#c7ebf8;
  --mist:#e9f6fb;
  --ink:#1f2a36;
  --footer:#1d1f24;
  --stage:#e6e9ed;
  --white:#ffffff;
}
*{box-sizing:border-box;margin:0;padding:0}
html,body{width:900px;height:1200px;overflow:hidden;background:var(--stage);font-family:"Open Sans",Arial,sans-serif;color:var(--ink)}
.spread{position:relative;width:900px;height:1200px}
.sheet{position:absolute;top:296px;width:600px;height:849px;background:var(--white);transform-origin:0 0;transform:scale(.7167);overflow:hidden;box-shadow:0 6px 22px rgba(0,0,0,.18)}
.sheet--consultancy{left:13px}
.sheet--recruitment{left:457px}
.sheet-art{position:absolute;inset:0;width:600px;height:849px}
.photo-area{position:absolute}

/* page one */
.brand{position:absolute;left:38px;top:118px;display:flex;align-items:center;gap:10px}
.brand-mark{width:16px;height:16px;border-radius:50%;background:var(--blue-mid)}
.brand-name{font-size:26px;font-weight:600;letter-spacing:1px;color:var(--navy)}
.tagline{position:absolute;left:38px;top:306px;width:300px;font-size:16px;line-height:1.3;font-weight:800;color:var(--white)}
.intro{position:absolute;left:38px;top:458px;width:520px}
.intro h1{font-size:20px;font-weight:800;color:var(--ink);margin-bottom:8px}
.intro p{font-size:10.5px;line-height:1.5;margin-bottom:8px}
.services{position:absolute;left:38px;top:618px;width:530px;display:grid;grid-template-columns:repeat(3,1fr);row-gap:14px;column-gap:10px}
.service{display:flex;align-items:center;gap:9px;font-size:11px;line-height:1.25;font-weight:600}
.service-icon{flex:none;width:44px;height:44px}
.footer{position:absolute;left:0;right:0;bottom:0;height:44px;background:var(--footer);display:flex;justify-content:space-around;align-items:center;color:var(--white);font-size:12px;font-weight:600}
.footer span{display:flex;align-items:center;gap:7px}
.footer svg{width:16px;height:16px}

/* page two */
.pillars{position:absolute;left:30px;top:258px;width:540px}
.pillar{display:flex;gap:12px;margin-bottom:7px}
.pillar-icon{flex:none;width:40px;height:40px}
.pillar h2{font-size:12.5px;line-height:1.2;font-weight:800;color:var(--blue-mid)}
.pillar p{font-size:7.2px;line-height:1.35}
.recruit{position:absolute;left:30px;top:470px;width:540px}
.recruit-label{display:inline-block;background:var(--blue-mid);color:var(--white);font-weight:800;font-size:11px;padding:2px 10px;margin-bottom:6px}
.recruit-cols{display:grid;grid-template-columns:1fr 1fr;gap:14px;font-size:7.2px;line-height:1.35}
.recruit-cols p{margin-bottom:4px}
.recruit-cols ul{list-style:none;margin-bottom:4px;display:grid;grid-template-columns:1fr 1fr;column-gap:8px}
.recruit-cols li{padding-left:10px;position:relative}
.recruit-cols li::before{content:"";position:absolute;left:0;top:2.5px;width:5px;height:5px;border-radius:50%;background:var(--blue-mid)}
.lead{font-weight:700}
.accent{color:var(--blue-mid);font-weight:700}
.skills{position:absolute;left:70px;right:20px;top:700px;height:105px;display:flex;flex-wrap:wrap;justify-content:center;align-items:baseline;align-content:center;gap:2px 12px;color:var(--blue-mid);font-weight:600;line-height:1.15}
.skills span{white-space:nowrap}
</style>
</head>
<body>
<main class="spread">

  <section class="sheet sheet--consultancy">
    <svg class="sheet-art" viewBox="0 0 600 849" aria-hidden="true">
      <defs>
        <linearGradient id="city" x1="0" y1="0" x2="1" y2="1">
          <stop offset="0" stop-color="#9fb4d6"/><stop offset="1" stop-color="#3f6aa6"/>
        </linearGradient>
        <linearGradient id="tech" x1="0" y1="0" x2="1" y2="1">
          <stop offset="0" stop-color="#16305c"/><stop offset=".6" stop-color="#3a5e94"/><stop offset="1" stop-color="#0d1e3d"/>
        </linearGradient>
      </defs>
      <polygon points="175,0 600,0 600,150 470,330" fill="url(#city)"/>
      <polygon points="160,0 175,0 470,330 458,338" fill="var(--navy)"/>
      <polygon points="0,212 470,332 392,436 0,436" fill="var(--blue-mid)"/>
      <polygon points="470,332 600,150 600,185 478,345" fill="var(--navy)"/>
      <polygon points="520,310 600,210 600,340" fill="var(--sky)"/>
      <polygon points="560,300 600,260 600,300" fill="var(--blue)"/>
    </svg>
    <div class="photo-area" role="img" aria-label="Photograph of glass office towers seen from below" style="left:300px;top:10px;width:280px;height:140px"></div>

    <div class="brand"><span class="brand-mark"></span><span class="brand-name">MERIDIAN APEX</span></div>
    <p class="tagline">A partner who brings new and innovative ideas to the table, through extensive industry experience and knowledge. Meridian will ensure you are prepared for growth.</p>

    <div class="intro">
      <h1>Meridian Consultancy</h1>
      <p>Meridian Apex is a bespoke consultancy firm that specialises in buy side investment. Through an industry based consultative approach we assist our clients in preparing for, and facilitating, long term growth. Working closely with our clients we combine innovative thinking and breakthrough technologies to accelerate progress and, together, achieve enduring results.</p>
      <p>Experienced in successfully delivering change for global organisations as well as assisting smaller firms during their growth phase. Meridian will work with you create a workable model and ensure</p>
    </div>

    <div class="services">
      <div class="service"><svg class="service-icon" viewBox="0 0 44 44"><circle cx="22" cy="22" r="21" fill="var(--blue-mid)"/><circle cx="22" cy="22" r="17" fill="none" stroke="#fff" stroke-width="1.2"/><rect x="15" y="13" width="12" height="16" fill="none" stroke="#fff" stroke-width="1.4"/><path d="M17 18h8M17 22h8M17 26h5" stroke="#fff" stroke-width="1.2"/></svg>Order<br>Management<br>and Trading</div>
      <div class="service"><svg class="service-icon" viewBox="0 0 44 44"><circle cx="22" cy="22" r="21" fill="var(--blue-mid)"/><circle cx="22" cy="22" r="17" fill="none" stroke="#fff" stroke-width="1.2"/><circle cx="16" cy="18" r="3" fill="none" stroke="#fff" stroke-width="1.4"/><circle cx="28" cy="18" r="3" fill="none" stroke="#fff" stroke-width="1.4"/><path d="M11 29c1-5 9-5 10 0M23 29c1-5 9-5 10 0" fill="none" stroke="#fff" stroke-width="1.4"/></svg>CRM/<br>Onboarding</div>
      <div class="service"><svg class="service-icon" viewBox="0 0 44 44"><circle cx="22" cy="22" r="21" fill="var(--blue-mid)"/><circle cx="22" cy="22" r="17" fill="none" stroke="#fff" stroke-width="1.2"/><path d="M15 14h14v17H15z M18 19l2 2 4-4 M18 26h8" fill="none" stroke="#fff" stroke-width="1.4"/></svg>Compliance</div>

      <div class="service"><svg class="service-icon" viewBox="0 0 44 44"><circle cx="22" cy="22" r="21" fill="var(--blue-mid)"/><circle cx="22" cy="22" r="17" fill="none" stroke="#fff" stroke-width="1.2"/><path d="M13 30h18M15 30v-5M20 30v-9M25 30v-7M30 30v-12M14 22l6-6 5 3 6-6" fill="none" stroke="#fff" stroke-width="1.4"/></svg>Investment<br>and<br>Research</div>
      <div class="service"><svg class="service-icon" viewBox="0 0 44 44"><circle cx="22" cy="22" r="21" fill="var(--blue-mid)"/><circle cx="22" cy="22" r="17" fill="none" stroke="#fff" stroke-width="1.2"/><circle cx="20" cy="20" r="6" fill="none" stroke="#fff" stroke-width="1.4"/><path d="M24.5 24.5l6 6" stroke="#fff" stroke-width="2"/></svg>Performance,<br>Risk and<br>Attribution</div>
      <div class="service"><svg class="service-icon" viewBox="0 0 44 44"><circle cx="22" cy="22" r="21" fill="var(--blue-mid)"/><circle cx="22" cy="22" r="17" fill="none" stroke="#fff" stroke-width="1.2"/><rect x="13" y="16" width="18" height="13" fill="none" stroke="#fff" stroke-width="1.4"/><path d="M13 20h18M18 24h8" stroke="#fff" stroke-width="1.2"/></svg>Finance<br>and<br>Accounting</div>

      <div class="service"><svg class="service-icon" viewBox="0 0 44 44"><circle cx="22" cy="22" r="21" fill="var(--blue-mid)"/><circle cx="22" cy="22" r="17" fill="none" stroke="#fff" stroke-width="1.2"/><circle cx="20" cy="21" r="6" fill="none" stroke="#fff" stroke-width="1.4"/><path d="M24.5 25.5l6 6M17 21h6" stroke="#fff" stroke-width="1.6"/></svg>Investment<br>and<br>Research</div>
      <div class="service"><svg class="service-icon" viewBox="0 0 44 44"><circle cx="22" cy="22" r="21" fill="var(--blue-mid)"/><circle cx="22" cy="22" r="17" fill="none" stroke="#fff" stroke-width="1.2"/><path d="M14 13h12v18H14z M17 18h6M17 22h6M17 26h4" fill="none" stroke="#fff" stroke-width="1.4"/><circle cx="27" cy="25" r="4" fill="var(--blue-mid)" stroke="#fff" stroke-width="1.4"/></svg>Client and<br>Regulatory<br>Reporting</div>
      <div class="service"><svg class="service-icon" viewBox="0 0 44 44"><circle cx="22" cy="22" r="21" fill="var(--blue-mid)"/><circle cx="22" cy="22" r="17" fill="none" stroke="#fff" stroke-width="1.2"/><rect x="13" y="18" width="18" height="12" fill="none" stroke="#fff" stroke-width="1.4"/><path d="M18 18v-3h8v3" fill="none" stroke="#fff" stroke-width="1.4"/></svg>Middle<br>and<br>Back Office</div>
    </div>

    <footer class="footer">
      <span><svg viewBox="0 0 16 16"><circle cx="8" cy="8" r="7" fill="none" stroke="#fff"/><path d="M5 4.5l2 2-1 1c.5 1 1.5 2 2.5 2.5l1-1 2 2-1.2 1.2C7.5 12 4 8.5 3.8 5.7z" fill="#fff"/></svg>+44 (0) 7700 900123</span>
      <span><svg viewBox="0 0 16 16"><circle cx="8" cy="8" r="7" fill="none" stroke="#fff"/><rect x="4" y="5.5" width="8" height="5" fill="none" stroke="#fff"/><path d="M4 5.5l4 3 4-3" fill="none" stroke="#fff"/></svg>info@meridianapex.com</span>
      <span><svg viewBox="0 0 16 16"><circle cx="8" cy="8" r="7" fill="none" stroke="#fff"/><ellipse cx="8" cy="8" rx="3" ry="6" fill="none" stroke="#fff"/><path d="M2 8h12" stroke="#fff"/></svg>www.meridianapex.com</span>
    </footer>
  </section>

  <section class="sheet sheet--recruitment">
    <svg class="sheet-art" viewBox="0 0 600 849" aria-hidden="true">
      <polygon points="140,0 600,0 600,140 455,248" fill="url(#tech)"/>
      <polygon points="125,0 140,0 455,248 444,256" fill="var(--navy)"/>
      <polygon points="455,248 600,140 600,170 462,262" fill="var(--navy)"/>
      <polygon points="515,240 600,175 600,280" fill="var(--sky)"/>
      <polygon points="0,712 600,690 600,805 0,805" fill="var(--pale)"/>
      <polygon points="0,740 600,712 600,805 0,805" fill="var(--mist)" opacity=".6"/>
      <polygon points="0,755 70,805 0,805" fill="var(--navy)"/>
      <polygon points="0,778 40,805 0,805" fill="var(--sky)"/>
    </svg>
    <div class="photo-area" role="img" aria-label="Photograph of a hand touching a glowing digital finance interface" style="left:260px;top:10px;width:320px;height:130px"></div>

    <div class="pillars">
      <div class="pillar"><svg class="pillar-icon" viewBox="0 0 44 44"><g fill="none" stroke="var(--blue-mid)" stroke-width="1.6"><circle cx="22" cy="22" r="9"/><path d="M22 8v5M22 31v5M8 22h5M31 22h5M12 12l3.5 3.5M28.5 28.5L32 32M12 32l3.5-3.5M28.5 15.5L32 12"/><path d="M18 22l3 3 5-6"/></g></svg><div><h2>Business Strategy</h2><p>Meridian will help you create a business strategy tailored to your requirements. Ensuring each business process is defined and taken into account allows for a successful design. Creating and implementing an operating model that takes into account budget, resources, culture and your company's vision.</p></div></div>
      <div class="pillar"><svg class="pillar-icon" viewBox="0 0 44 44"><g fill="none" stroke="var(--blue-mid)" stroke-width="1.6"><circle cx="13" cy="16" r="6"/><path d="M10 24h6v4h-6z"/><circle cx="31" cy="30" r="6"/><path d="M22 12h8l-3-3M30 12l-3 3M22 32h-6l3 3"/></g></svg><div><h2>Change management</h2><p>Meridian works with clients to deliver bespoke change initiatives. Rigorous business analysis and risk management allows for successful change initiatives. We work with you throughout the complete process to ensure that delivery is based on value. Transition phases are challenging aspects of change initiatives which is why our team manage all transitions and the risk they carry.</p></div></div>
      <div class="pillar"><svg class="pillar-icon" viewBox="0 0 44 44"><g fill="none" stroke="var(--blue-mid)" stroke-width="1.6"><rect x="8" y="12" width="28" height="18"/><path d="M16 36h12M22 30v6"/><circle cx="22" cy="21" r="4"/><path d="M22 14v3M22 25v3M15 21h3M26 21h3"/></g></svg><div><h2>IT transformation</h2><p>Meridian is widely experienced in a range of technologies. We help with the implementation of software provider or design and develop bespoke services. Covering front to back office the team specialises in full project lifecycle from feasibility through to implementation.</p></div></div>
      <div class="pillar"><svg class="pillar-icon" viewBox="0 0 44 44"><g fill="none" stroke="var(--blue-mid)" stroke-width="1.6"><circle cx="22" cy="12" r="6"/><path d="M22 18v6M10 24h24M10 24v5M34 24v5M22 24v5"/><rect x="6" y="29" width="8" height="7"/><rect x="18" y="29" width="8" height="7"/><rect x="30" y="29" width="8" height="7"/></g></svg><div><h2>Organisational structure</h2><p>Meridian works with clients to improve resource capability and strategic partnerships. Acting as an extension of the HR function, we analyse business processes and ensure that our clients have the ability to manage changing workforce demands.</p></div></div>
    </div>

    <div class="recruit">
      <span class="recruit-label">MERIDIAN RECRUITMENT</span>
      <div class="recruit-cols">
        <div>
          <p class="lead">A partner who brings new and innovative ideas to the table, through extensive industry experience and knowledge. Meridian will ensure you are prepared for growth.</p>
          <p>Meridian is more than an ordinary recruitment service. Our experts work with clients to understand current and impending organisational needs, using research to effectively benchmark. We are developing communities that provide effective, and timely, recruitment solutions for our clients.</p>
          <p><span class="accent">Specialists in:</span> Asset Management recruitment with a specialisation in I.T., Operations, Regulation and Change Management.</p>
          <p>Meridian acts as an extension of your HR function, providing an end-to-end permanent &amp; contingent talent acquisition solution, taking full accountability and ownership for the entire recruitment process, which includes:</p>
          <ul><li>Workforce Planning</li><li>Candidate Management</li><li>Strategic Sourcing</li><li>Weekly vacancy updates</li><li>Talent Engagement</li></ul>
        </div>
        <div>
          <p>We recognise that hiring can be a lengthy process, therefore we partner with you to ensure you only interview top quality candidates, cutting out multiple meetings with multiple candidates. Giving hiring managers time back in their diaries to do their day jobs and reducing the time to hire. This is achieved by:</p>
          <ul><li>Understanding the roles and partnering with you to build meaningful job descriptions</li><li>Support with interviews and we ensure the candidate has a positive experience</li><li>Candidates are fully screened and interviewed prior to presentation to you</li><li>Qualified shortlist of top 3 candidates</li></ul>
          <p>Meridian recruitment partners with principal business consultants to ensure candidates are properly screened before presenting to our clients. This allows for our clients to focus on only interviewing the best on the market.</p>
        </div>
      </div>
    </div>

    <div class="skills" aria-label="Specialist skill areas">
      <span style="font-size:12px">Trading Platforms</span>
      <span style="font-size:10px">MIS</span>
      <span style="font-size:16px">Cloud Stack</span>
      <span style="font-size:7px">Settlement</span>
      <span style="font-size:12px">FIX/Swift</span>
      <span style="font-size:16px">Fixed Income</span>
      <span style="font-size:7px">NoSQL</span>
      <span style="font-size:14px">Workflow Management</span>
      <span style="font-size:7px">Collateral Management</span>
      <span style="font-size:18px">Connectivity</span>
      <span style="font-size:10px">Equity</span>
      <span style="font-size:20px;font-weight:700">SQL</span>
      <span style="font-size:8px">XML</span>
      <span style="font-size:8px">Pricing and analytics</span>
      <span style="font-size:16px">Reference data</span>
      <span style="font-size:11px">Batch processing</span>
      <span style="font-size:12px">Business Intelligence</span>
      <span style="font-size:12px">Risk and attribution</span>
    </div>

    <footer class="footer">
      <span><svg viewBox="0 0 16 16"><circle cx="8" cy="8" r="7" fill="none" stroke="#fff"/><path d="M5 4.5l2 2-1 1c.5 1 1.5 2 2.5 2.5l1-1 2 2-1.2 1.2C7.5 12 4 8.5 3.8 5.7z" fill="#fff"/></svg>+44 (0) 7700 900123</span>
      <span><svg viewBox="0 0 16 16"><circle cx="8" cy="8" r="7" fill="none" stroke="#fff"/><rect x="4" y="5.5" width="8" height="5" fill="none" stroke="#fff"/><path d="M4 5.5l4 3 4-3" fill="none" stroke="#fff"/></svg>info@meridianapex.com</span>
      <span><svg viewBox="0 0 16 16"><circle cx="8" cy="8" r="7" fill="none" stroke="#fff"/><ellipse cx="8" cy="8" rx="3" ry="6" fill="none" stroke="#fff"/><path d="M2 8h12" stroke="#fff"/></svg>www.meridianapex.com</span>
    </footer>
  </section>

</main>
</body>
</html>
```